BLS Business Card 2018

Larkmere Chiropractic. We have two locations that we want to advertise on the same card. Brightvale OrthoCore campus address: 3815 Pellham Dr., Suite 240, Flowood, MS 39417. Madison address: 246 Willowmere Dr., Building D., Madison, MS 39284. website: www.drlarkmere-example.com. o:(601)555-0147 f:(601)555-0183

Target Market(s)

Health care decision makers: primary care doctors and mothers

Contact Information for Business Card

I have no idea; up for any suggestions and I'd do much better picking from examples versus describing what I'm looking for. We are in a very high end location and would like the cards to look really sharp.

Requirements
Must have
• My name, Martin R Belvane, D.C.

```html
<!DOCTYPE html>
<html lang="en">
<head>
<meta charset="utf-8">
<title>Larkmere Chiropractic – Business Card</title>
<link rel="stylesheet" href="https://fonts.googleapis.com/css2?family=Roboto:wght@400&family=Roboto+Condensed:wght@700&display=swap">
<style>
  :root {
    --backdrop: #7b5034;
    --card: #f6f6f6;
    --ink: #111111;
    --text: #555555;
    --muted: #5c5c5c;
    --art-light: #f1f1f1;
    --art-mid: #dcdcdc;
    --shadow: rgba(0, 0, 0, 0.45);
  }
  * { margin: 0; padding: 0; box-sizing: border-box; }
  html, body { width: 1200px; height: 960px; overflow: hidden; }
  body {
    position: relative;
    background: var(--backdrop);
    font-family: "Roboto", Arial, sans-serif;
  }
  .card {
    position: absolute;
    width: 600px;
    height: 343px;
    background: var(--card);
    box-shadow: 2px 3px 5px var(--shadow);
    overflow: hidden;
  }
  .card--front { left: 314px; top: 113px; }
  .card--back { left: 311px; top: 472px; }

  .name-marker {
    position: absolute;
    left: 0; top: 50px;
    width: 12px; height: 40px;
    background: var(--ink);
  }
  .holder-name {
    position: absolute;
    left: 37px; top: 57px;
    font-family: "Roboto Condensed", "Arial Narrow", sans-serif;
    font-weight: 700;
    font-size: 20px;
    color: var(--ink);
    letter-spacing: 0.2px;
  }
  .location {
    position: absolute;
    left: 37px;
    font-size: 14px;
    line-height: 18.5px;
    color: var(--text);
  }
  .location--campus { top: 123px; }
  .location--madison { top: 184px; }

  .contact-list {
    position: absolute;
    left: 37px; top: 248px;
    list-style: none;
    font-size: 14px;
    line-height: 19.5px;
    color: var(--text);
  }
  .contact-list li { display: flex; align-items: center; }
  .contact-icon { width: 14px; height: 14px; margin-right: 10px; fill: #111; }

  .figure-art {
    position: absolute;
    right: 10px; top: 12px;
    width: 260px; height: 331px;
    background: radial-gradient(ellipse at 55% 50%, var(--art-mid) 0%, var(--art-light) 60%, var(--card) 100%);
  }

  .brand {
    position: absolute;
    left: 0; right: 0; top: 122px;
    display: flex;
    align-items: center;
    justify-content: center;
    gap: 14px;
  }
  .brand-mark {
    width: 22px; height: 22px;
    border-radius: 50%;
    background: var(--ink);
  }
  .brand-name {
    font-size: 34px;
    font-weight: 400;
    color: var(--ink);
    letter-spacing: 0.5px;
  }
  .website {
    position: absolute;
    left: 0; right: 0; top: 282px;
    text-align: center;
    font-size: 14px;
    letter-spacing: 5px;
    color: var(--muted);
  }
</style>
</head>
<body>
  <section class="card card--front">
    <div class="name-marker"></div>
    <h1 class="holder-name">MARTIN R BELVANE, D.C.</h1>

    <address class="location location--campus">
      Brightvale OrthoCore campus :<br>
      3815 Pellham Dr., Suite 240<br>
      Flowood, MS 39417.
    </address>

    <address class="location location--madison">
      Madison address:<br>
      246 Willowmere Dr., Building D.<br>
      Madison, MS 39284.
    </address>

    <ul class="contact-list">
      <li>
        <svg class="contact-icon" viewBox="0 0 16 16" aria-hidden="true"><path d="M3.6 1.2 6 3.6 4.6 5.4c.8 1.9 2.2 3.3 4 4.2l1.6-1.4 2.6 2.4-1.6 2.4C6.6 12.6 2.8 8.6 1.4 3.4z"/></svg>
        (601)555-0147
      </li>
      <li>
        <svg class="contact-icon" viewBox="0 0 16 16" aria-hidden="true"><rect x="4" y="1.5" width="8" height="4"/><rect x="1" y="6" width="14" height="6" rx="1"/><rect x="4" y="10" width="8" height="4.5" fill="#f6f6f6" stroke="#111" stroke-width="1.2"/></svg>
        (601)555-0183
      </li>
      <li>
        <svg class="contact-icon" viewBox="0 0 16 16" aria-hidden="true"><circle cx="8" cy="8" r="6.5"/><path d="M5 4.5c1.5.5 2 1.5 1.2 2.6-.8 1 .4 2 1.4 2.4.8.4.4 2-.4 3M10 3.5c-.5 1 .3 2 1.5 2.1M11.8 9c-1 .3-1.6 1.2-1.2 2.4" stroke="#f6f6f6" stroke-width="1.3" fill="none"/></svg>
        www.drlarkmere-example.com
      </li>
    </ul>

    <div class="figure-art" role="img" aria-label="Loose black line sketch of a stretching human torso with raised arm"></div>
  </section>

  <section class="card card--back">
    <div class="brand">
      <span class="brand-mark"></span>
      <span class="brand-name">Larkmere Chiropractic</span>
    </div>
    <p class="website">WWW.DRLARKMERE-EXAMPLE.COM</p>
  </section>
</body>
</html>
```